Looking for a modern, Professional business card design

We have a simple business card, but are looking for a more modern, professional look. A sample of the basic card is attached as well as the logo. We would also like to add that we offer:
Struggling with your finances?
- Learn to become debt free
- Discover the power of cash
- Control your money instead of it controlling you
Let us help you achieve a new level of financial freedom!
Also, we would like to have a "SPECIAL OFFER!: FREE 30 minute consultation"
Financial Planning

```html
<!DOCTYPE html>
<html lang="en">
<head>
<meta charset="utf-8">
<title>Steady Ledger Coaching – Business Card</title>
<link rel="stylesheet" href="https://fonts.googleapis.com/css2?family=Source+Sans+3:ital,wght@0,400;0,600;0,700;1,400;1,700&display=swap">
<style>
  :root {
    --backdrop: #4a4a4a;
    --card-white: #ffffff;
    --card-black: #000000;
    --green: #3f9a3c;
    --green-dark: #2f8a34;
    --lime: #b4d335;
    --lime-text: #7cc142;
    --ink: #1e1e1e;
    --grey-text: #555555;
    --divider: #c9c9c9;
  }
  * { box-sizing: border-box; margin: 0; padding: 0; }
  html, body {
    width: 1105px;
    height: 1200px;
    overflow: hidden;
    background: var(--backdrop);
    font-family: "Source Sans 3", Arial, sans-serif;
  }
  .card {
    position: absolute;
    left: 193px;
    width: 719px;
    height: 412px;
    box-shadow: 0 4px 10px rgba(0, 0, 0, 0.45);
    overflow: hidden;
  }
  /* Front */
  .card--front { top: 181px; background: var(--card-white); }
  .brand {
    position: absolute;
    display: flex;
    align-items: center;
    gap: 10px;
    font-weight: 700;
    color: var(--green);
    white-space: nowrap;
  }
  .brand__dot {
    width: 16px; height: 16px;
    border-radius: 50%;
    background: var(--green);
    flex: none;
  }
  .card--front .brand { left: 26px; top: 168px; font-size: 25px; }
  .divider {
    position: absolute;
    left: 321px; top: 118px;
    width: 1px; height: 172px;
    background: var(--divider);
  }
  .contact { position: absolute; left: 350px; top: 120px; }
  .contact__name { font-size: 25px; font-weight: 600; color: var(--green); line-height: 1.2; }
  .contact__role { font-size: 19px; color: var(--ink); margin-top: 3px; }
  .contact__list { list-style: none; margin-top: 18px; }
  .contact__item {
    display: flex; align-items: center; gap: 12px;
    font-size: 18px; color: var(--grey-text); line-height: 28px;
  }
  .contact__icon { width: 16px; height: 16px; flex: none; fill: var(--green); }
  .front-band-line {
    position: absolute; left: 0; right: 0; bottom: 33px;
    height: 3px; background: #1a1a1a;
  }
  .front-band {
    position: absolute; left: 0; right: 0; bottom: 0;
    height: 31px;
    background: linear-gradient(90deg, var(--green-dark) 0%, var(--lime) 50%, var(--green-dark) 100%);
  }
  /* Back */
  .card--back { top: 637px; background: var(--card-black); text-align: center; }
  .card--back .brand {
    left: 0; right: 0; top: 95px;
    justify-content: center; font-size: 34px;
  }
  .pitch { position: absolute; left: 0; right: 0; top: 222px; }
  .pitch__title { font-size: 20px; font-weight: 600; color: var(--green); letter-spacing: 0.3px; }
  .pitch__lines { list-style: none; margin-top: 2px; }
  .pitch__lines li { font-size: 18px; font-style: italic; color: #ffffff; line-height: 25px; }
  .pitch__bullet { color: var(--green); font-style: normal; margin: 0 4px; }
  .offer {
    position: absolute; left: 0; right: 0; top: 342px;
    font-size: 25px; font-weight: 700; font-style: italic; color: var(--lime-text);
  }
</style>
</head>
<body>
  <section class="card card--front" aria-label="Business card front">
    <div class="brand"><span class="brand__dot"></span>Steady Ledger Coaching</div>
    <div class="divider"></div>
    <div class="contact">
      <p class="contact__name">Daniel R. Hayes</p>
      <p class="contact__role">Personal Financial Coach</p>
      <ul class="contact__list">
        <li class="contact__item">
          <svg class="contact__icon" viewBox="0 0 16 16" aria-hidden="true"><path d="M4 0h8a1 1 0 0 1 1 1v14a1 1 0 0 1-1 1H4a1 1 0 0 1-1-1V1a1 1 0 0 1 1-1zm1 2v10h6V2zm3 11a1 1 0 1 0 0 2 1 1 0 0 0 0-2z"/></svg>
          (205) 555-0148
        </li>
        <li class="contact__item">
          <svg class="contact__icon" viewBox="0 0 16 16" aria-hidden="true"><path d="M1 3h14v1.2L8 9 1 4.2zm0 2.6 7 4.8 7-4.8V13H1z"/></svg>
          daniel@steadyledgercoach.com
        </li>
        <li class="contact__item">
          <svg class="contact__icon" viewBox="0 0 16 16" aria-hidden="true"><circle cx="8" cy="8" r="7.5"/><path d="M1 8h14M8 .5c-2.5 3-2.5 12 0 15M8 .5c2.5 3 2.5 12 0 15" stroke="#fff" stroke-width="1" fill="none"/></svg>
          www.steadyledgercoach.com
        </li>
      </ul>
    </div>
    <div class="front-band-line"></div>
    <div class="front-band"></div>
  </section>

  <section class="card card--back" aria-label="Business card back">
    <div class="brand"><span class="brand__dot"></span>Steady Ledger Coaching</div>
    <div class="pitch">
      <p class="pitch__title">STRUGGLING WITH YOUR FINANCES?</p>
      <ul class="pitch__lines">
        <li>Learn to become debt free <span class="pitch__bullet">•</span> Discover the power of cash</li>
        <li>Control your money instead of it controlling you</li>
        <li>Let us help you achieve a new level of financial freedom!</li>
      </ul>
    </div>
    <p class="offer">SPECIAL OFFER!: FREE 30 minute consultation</p>
  </section>
</body>
</html>
```